Brightfen Business Card Redesign & Logo Update

We need to update our business cards to something more modern and fresh. Brightfen can provide the current color schemes and old design examples, but welcome creativity in helping us with this redesign. PLEASE NOTE that we no longer utilize the "tree" and/or "leaf" imagery in our branding. If able would apprecaite an update on the quality of our "words only" logo in Ai. / PNG formats too.

Target Market(s)

Investors, landowners, corporate partners, contractors

Industry/Entity Type

Environmental Restoration & Conservation

Contact Information for Business Card

Logo, persons name, title, mailing address, phone and email, website url

Font styles to use
Other font styles liked:
• Merriweather

Requirements
Nice to have
• Logo, persons name, title, mailing address, phone and email, website url, but open to ideams
Should not have
• No all back backgrounds

```html
<!DOCTYPE html>
<html lang="en">
<head>
<meta charset="utf-8">
<title>Brightfen Business Card</title>
<link rel="stylesheet" href="https://fonts.googleapis.com/css2?family=Oswald:wght@500;700&family=Merriweather:wght@400;700&display=swap">
<style>
  :root {
    --stage: #a3a3a3;
    --card: #ffffff;
    --green: #167a3a;
    --orange: #ec7d23;
    --ink: #141414;
  }
  * { box-sizing: border-box; margin: 0; padding: 0; }
  html, body { width: 1146px; height: 1200px; overflow: hidden; }
  body { background: var(--stage); position: relative; }

  .card {
    position: absolute;
    left: 176px;
    width: 797px;
    background: var(--card);
    overflow: hidden;
  }
  .card--front { top: 113px; height: 455px; }
  .card--back { top: 595px; height: 468px; }

  .wordmark {
    position: absolute;
    left: 0; right: 0;
    text-align: center;
    font-family: "Oswald", sans-serif;
    font-weight: 700;
    color: var(--green);
    line-height: 1;
    letter-spacing: 1px;
  }
  .tagline {
    position: absolute;
    left: 0; right: 0;
    text-align: center;
    font-family: "Oswald", sans-serif;
    font-weight: 700;
    color: var(--ink);
    line-height: 1;
    letter-spacing: 0.3px;
  }
  .card--front .wordmark { top: 172px; font-size: 84px; }
  .card--front .tagline { top: 268px; font-size: 20px; }
  .card--back .wordmark { top: 72px; font-size: 76px; }
  .card--back .tagline { top: 160px; font-size: 18px; }

  .person {
    position: absolute;
    right: 415px;
    top: 268px;
    text-align: right;
    font-family: "Merriweather", serif;
  }
  .person__name {
    font-weight: 700;
    font-size: 24px;
    color: var(--orange);
    line-height: 1.2;
  }
  .person__name .surname { color: var(--green); }
  .person__title {
    font-size: 19px;
    color: var(--ink);
    margin-top: 8px;
  }

  .divider {
    position: absolute;
    left: 384px;
    top: 252px;
    width: 2px;
    height: 98px;
    background: var(--green);
  }

  .contacts {
    position: absolute;
    left: 398px;
    top: 257px;
    list-style: none;
    font-family: "Merriweather", serif;
    font-size: 20px;
    color: var(--ink);
  }
  .contacts li {
    display: flex;
    align-items: center;
    gap: 7px;
    height: 29px;
  }
  .contacts svg { width: 15px; height: 15px; fill: var(--green); flex: none; }

  .address {
    position: absolute;
    left: 0; right: 0;
    top: 380px;
    text-align: center;
    font-family: "Merriweather", serif;
    font-size: 20px;
    color: var(--ink);
  }

  .footer-band {
    position: absolute;
    left: 0;
    bottom: 0;
    width: 797px;
    height: 30px;
  }
</style>
</head>
<body>

  <section class="card card--front">
    <div class="wordmark">BRIGHTFEN</div>
    <div class="tagline">ENVIRONMENTAL CREDIT COMPANY</div>
  </section>

  <section class="card card--back">
    <div class="wordmark">BRIGHTFEN</div>
    <div class="tagline">ENVIRONMENTAL CREDIT COMPANY</div>

    <div class="person">
      <div class="person__name">MARCUS <span class="surname">HALE</span></div>
      <div class="person__title">Founder</div>
    </div>

    <div class="divider"></div>

    <ul class="contacts">
      <li>
        <svg viewBox="0 0 16 16" aria-hidden="true"><path d="M1 6c0-2 3-4 7-4s7 2 7 4v1h-4V5.5H5V7H1zM3 8h10l1 6H2zm5 1.5a2 2 0 1 0 0 4 2 2 0 0 0 0-4z"/></svg>
        (555) 014-2287
      </li>
      <li>
        <svg viewBox="0 0 16 16" aria-hidden="true"><path d="M1 3h14v1.2L8 9 1 4.2zM1 6l7 4.8L15 6v7H1z"/></svg>
        hello@brightfenmail.com
      </li>
      <li>
        <svg viewBox="0 0 16 16" aria-hidden="true"><circle cx="8" cy="8" r="7"/><path d="M4 5h3l1 2-2 1 1 3-2 1-1-3zM10 4l2 1-1 2h2v3l-2 1-1-2z" fill="#fff"/></svg>
        www.brightfen-example.com
      </li>
    </ul>

    <div class="address">Fenway Office Park, Rd No. 48, PO 2210, BD</div>

    <svg class="footer-band" viewBox="0 0 797 30" aria-hidden="true">
      <polygon points="0,0 400,0 377,30 0,30" fill="var(--green)"/>
      <polygon points="410,0 797,0 797,30 387,30" fill="var(--orange)"/>
    </svg>
  </section>

</body>
</html>
```